Construction Company

Design a clutter free business card, it can be double-sided utilizing the logo for VKM Ltd simple with all relevant contact information.

Please also a letterhead design to function for the purposes of invoicing, all mail requirements, with header to be distinctive while the footer ties page together and incorporates all necessary information.

For now, please use generic / dummy text and when a winner is selected, I will disclose the contact information.

Hi Designers! Please read the updated brief which includes the design of a business card and letterhead. Thank you!

```html
<!DOCTYPE html>
<html lang="en">
<head>
<meta charset="utf-8">
<title>VKM Ltd – Business Card</title>
<link rel="stylesheet" href="https://fonts.googleapis.com/css2?family=Cinzel:wght@500;600&family=Open+Sans:wght@400&display=swap">
<style>
  :root {
    --stage: #d6d6d8;
    --card: #2a2a2a;
    --card-edge: #1f1f1f;
    --gold: #c9a227;
    --white: #f4f4f4;
    --soft: #cfcfcf;
  }
  * { margin: 0; padding: 0; box-sizing: border-box; }
  html, body { width: 1200px; height: 834px; overflow: hidden; }
  body {
    background: var(--stage);
    display: flex;
    flex-direction: column;
    align-items: center;
    justify-content: center;
    gap: 34px;
  }
  .card {
    position: relative;
    width: 640px;
    height: 366px;
    background: var(--card);
    border: 1px solid var(--card-edge);
    border-radius: 4px;
    box-shadow: 0 6px 18px rgba(0,0,0,0.25);
    overflow: hidden;
  }
  .brand {
    display: flex;
    align-items: center;
    gap: 12px;
  }
  .brand-dot {
    width: 14px; height: 14px;
    border-radius: 50%;
    background: var(--gold);
  }
  .brand-name {
    font-family: "Cinzel", serif;
    font-weight: 600;
    color: var(--white);
    letter-spacing: 2px;
    white-space: nowrap;
  }
  /* back side */
  .card-back .brand {
    position: absolute;
    left: 50%; top: 128px;
    transform: translateX(-50%);
  }
  .card-back .brand-name { font-size: 58px; }
  .card-back .website {
    position: absolute;
    left: 0; right: 0; top: 232px;
    text-align: center;
    font-family: "Open Sans", sans-serif;
    font-size: 15px;
    color: var(--white);
    letter-spacing: 0.5px;
  }
  /* front side */
  .holder { position: absolute; left: 44px; top: 40px; }
  .holder-name {
    font-family: "Cinzel", serif;
    font-weight: 500;
    font-size: 24px;
    color: var(--gold);
    letter-spacing: 1px;
  }
  .holder-role {
    font-family: "Open Sans", sans-serif;
    font-size: 14px;
    color: var(--soft);
    margin-top: 2px;
  }
  .contact-list {
    position: absolute;
    left: 44px; bottom: 44px;
    list-style: none;
    font-family: "Open Sans", sans-serif;
    font-size: 15px;
    color: var(--white);
  }
  .contact-list li {
    display: flex;
    align-items: center;
    gap: 12px;
    line-height: 28px;
  }
  .contact-list svg { width: 14px; height: 14px; flex: none; }
  .card-front .brand {
    position: absolute;
    right: 48px; bottom: 52px;
  }
  .card-front .brand-name { font-size: 46px; }
</style>
</head>
<body>

  <section class="card card-back" aria-label="Business card back">
    <div class="brand">
      <span class="brand-dot"></span>
      <span class="brand-name">VKM Ltd</span>
    </div>
    <p class="website">www.vkmltd.com</p>
  </section>

  <section class="card card-front" aria-label="Business card front">
    <div class="holder">
      <h1 class="holder-name">Daniel Carter</h1>
      <p class="holder-role">Manager</p>
    </div>

    <ul class="contact-list">
      <li>
        <svg viewBox="0 0 24 24" aria-hidden="true"><path fill="var(--gold)" d="M6.6 10.8a15.1 15.1 0 0 0 6.6 6.6l2.2-2.2a1 1 0 0 1 1-.25 11.4 11.4 0 0 0 3.6.57 1 1 0 0 1 1 1V20a1 1 0 0 1-1 1A17 17 0 0 1 3 4a1 1 0 0 1 1-1h3.5a1 1 0 0 1 1 1c0 1.25.2 2.45.57 3.57a1 1 0 0 1-.25 1z"/></svg>
        <span>555-014-2738</span>
      </li>
      <li>
        <svg viewBox="0 0 24 24" aria-hidden="true"><rect x="2.5" y="5" width="19" height="14" rx="1.5" fill="none" stroke="var(--gold)" stroke-width="2"/><path d="M3 6l9 7 9-7" fill="none" stroke="var(--gold)" stroke-width="2"/></svg>
        <span>hello@vkmltd.com</span>
      </li>
      <li>
        <svg viewBox="0 0 24 24" aria-hidden="true"><circle cx="12" cy="12" r="9.5" fill="none" stroke="var(--gold)" stroke-width="2"/><path d="M2.5 12h19M12 2.5c3 3 3 16 0 19M12 2.5c-3 3-3 16 0 19" fill="none" stroke="var(--gold)" stroke-width="1.6"/></svg>
        <span>www.vkmltd.com</span>
      </li>
    </ul>

    <div class="brand">
      <span class="brand-dot"></span>
      <span class="brand-name">VKM Ltd</span>
    </div>
  </section>

</body>
</html>
```